New Business Card for Web Design/Internet Marketing Company

Looking for a great looking new business card. We are a 10 year old web design, internet marketing and website management company that works mostly with small businesses.

Our new card needs to better match the colors and style of our website, be bold, extremely usable and slightly edgy.

Target Market(s)

Small/Medium businesses that have websites

Industry/Entity Type

Internet

Requirements
Must have
• Front and back design, full color, rounded corners please

Must use the colors/style of our website (JPG provided)

INFO FOR CARDS (as readable as possible please)
Mark Lenner
President/CEO
mark@trelvanmedia.example
Phone: 520-381-7459
Toll Free: 866-381-7459
Address: 4315 W. Calloway Ave. Ste. 140, Tucson, AZ 85792

THINGS I WANT TO PROMOTE (if there is room):
1. Our Website - www.trelvanmedia.example

2. Social Media
Twitter: @trelvanmedia
Facebook: www.facebook.com/trelvanmedia

3. Our Services
Web Design
Internet Marketing
Website Management

```html
<!DOCTYPE html>
<html lang="en">
<head>
<meta charset="utf-8">
<title>Trelvan Media – Business Card</title>
<link href="https://fonts.googleapis.com/css2?family=Open+Sans:wght@400;600;700;800&display=swap" rel="stylesheet">
<style>
  :root {
    --orange: #f08a2c;
    --blue: #1a8cc4;
    --ink: #555a5e;
    --muted: #7b7f83;
    --rule: #c9c9c9;
    --card: #ffffff;
    --backdrop: #e9e7e4;
  }
  * { margin: 0; padding: 0; box-sizing: border-box; }
  html, body {
    width: 1200px; height: 400px; overflow: hidden;
    background: var(--backdrop);
    font-family: "Open Sans", Arial, sans-serif;
  }
  .stage { position: relative; width: 1200px; height: 400px; }
  .card {
    position: absolute; top: 45px; width: 523px; height: 300px;
    background: var(--card); border-radius: 4px; overflow: hidden;
    box-shadow: 0 2px 6px rgba(0,0,0,.18);
  }
  .card--front { left: 55px; }
  .card--back { left: 617px; }

  /* front */
  .holder {
    position: absolute; top: 22px; left: 0; width: 100%; text-align: center;
    font-size: 18px; font-weight: 700; color: var(--orange);
  }
  .holder .role { font-size: 15px; font-weight: 400; color: var(--blue); margin-left: 4px; }

  .brand { position: absolute; display: flex; flex-direction: column; }
  .brand__row { display: flex; align-items: center; gap: 8px; }
  .brand__dot { width: 16px; height: 16px; border-radius: 50%; background: var(--orange); flex: none; }
  .brand__name { font-weight: 700; color: var(--blue); letter-spacing: -0.5px; white-space: nowrap; }
  .brand__tagline { color: var(--muted); font-weight: 400; }

  .card--front .brand { left: 28px; top: 170px; align-items: flex-end; width: 232px; }
  .card--front .brand__name { font-size: 30px; }
  .card--front .brand__tagline { font-size: 13px; margin-top: 2px; }

  .divider { position: absolute; left: 283px; top: 95px; width: 1px; height: 140px; background: var(--rule); }

  .contact { position: absolute; left: 303px; top: 106px; list-style: none; font-size: 13px; color: var(--ink); }
  .contact li { display: flex; align-items: center; height: 19px; }
  .contact svg { width: 11px; height: 11px; margin-right: 8px; fill: var(--ink); flex: none; }
  .address { position: absolute; left: 303px; top: 196px; font-size: 13px; line-height: 19px; color: var(--ink); font-style: normal; }

  .footer-band { position: absolute; left: 0; bottom: 0; width: 100%; height: 12px; }

  /* back */
  .card--back .brand { left: 70px; width: 385px; top: 80px; align-items: flex-end; }
  .card--back .brand__name { font-size: 42px; }
  .card--back .brand__dot { width: 20px; height: 20px; }
  .card--back .brand__tagline { font-size: 14px; margin-top: 0; }

  .services { position: absolute; top: 181px; left: 0; width: 100%; text-align: center; list-style: none; font-size: 17px; font-weight: 700; color: var(--blue); line-height: 23px; }
  .services li { display: inline-block; margin: 0 6px; }
  .services li::before { content: ""; display: inline-block; width: 8px; height: 8px; border-radius: 50%; background: var(--orange); margin-right: 7px; vertical-align: 2px; }

  .social { position: absolute; top: 253px; left: 0; width: 100%; display: flex; justify-content: center; gap: 26px; font-size: 16px; color: var(--ink); }
  .social span { display: flex; align-items: center; }
  .social i { width: 14px; height: 14px; background: var(--blue); border-radius: 2px; margin-right: 6px; display: inline-block; }
</style>
</head>
<body>
<main class="stage">

  <section class="card card--front" aria-label="Card front">
    <p class="holder">Mark Lenner ,<span class="role">President/CEO</span></p>

    <div class="brand">
      <div class="brand__row"><span class="brand__dot"></span><span class="brand__name">Trelvan Media</span></div>
      <span class="brand__tagline">Websites that Work</span>
    </div>

    <div class="divider"></div>

    <ul class="contact">
      <li><svg viewBox="0 0 12 12"><path d="M2.5 1l2 2.2-1 1.3c.7 1.6 1.8 2.7 3.4 3.4l1.3-1 2.2 2-1.2 1.6C5 10.2 1.8 7 .9 2.2z"/></svg>866-381-7459</li>
      <li><svg viewBox="0 0 12 12"><path d="M2.5 1l2 2.2-1 1.3c.7 1.6 1.8 2.7 3.4 3.4l1.3-1 2.2 2-1.2 1.6C5 10.2 1.8 7 .9 2.2z"/></svg>520-381-7459</li>
      <li><svg viewBox="0 0 12 12"><path d="M1 3h10v7H1zM1.6 3.4L6 7l4.4-3.6v1L6 8 1.6 4.4z" fill-rule="evenodd"/></svg>mark@trelvanmedia.example</li>
      <li><svg viewBox="0 0 12 12"><circle cx="6" cy="6" r="5"/></svg>www.trelvanmedia.example</li>
    </ul>

    <address class="address">4315 W. Calloway Ave. Ste. 140<br>Tucson, AZ 85792</address>

    <svg class="footer-band" viewBox="0 0 523 12" preserveAspectRatio="none">
      <polygon points="0,0 268,0 256,12 0,12" fill="var(--blue)"/>
      <polygon points="274,0 523,0 523,12 262,12" fill="var(--orange)"/>
    </svg>
  </section>

  <section class="card card--back" aria-label="Card back">
    <div class="brand">
      <div class="brand__row"><span class="brand__dot"></span><span class="brand__name">Trelvan Media</span></div>
      <span class="brand__tagline">Websites that Work</span>
    </div>

    <ul class="services">
      <li>Web Design</li><li>Internet Marketing</li><br><li>Website Management</li>
    </ul>

    <div class="social">
      <span><i></i>@trelvanmedia</span>
      <span><i></i>trelvanmedia</span>
    </div>
  </section>

</main>
</body>
</html>
```